Modern Medical Optometry Website

We need mordern, Patient friendly website. Easy to navigate and enhance our advance medical technology and excellent patient care.
1. HOME PAGE
2. OUR TEAM PAGE
3. EYECARE PAGE - VISION SERVICES, EYE EXAMS, KERATOCONUS CENTER, GLAUCOMA , DIABITES, MELORIDEX EXAM, DIGITAL RETINAL, OCT.
4. MYOPIA CONTROL CLINIC
5. DRY EYE CLINIC
6. EYEWEAR
7. PATIENT CENTER - BLOG
7. CONTACT US
This is our current website www.brivaloka.com
and We want to add more content and a cleaner design like these website
http://tarnwickfolvendale.com/
https://www.qmvorlu.com/

```html
<!DOCTYPE html>
<html lang="en">
<head>
<meta charset="utf-8">
<title>Eye Glass Lenses – Lumivo Optometry</title>
<link href="https://fonts.googleapis.com/css2?family=Montserrat:wght@400;600;700&family=Open+Sans:wght@400;600;700&display=swap" rel="stylesheet">
<style>
:root{
  --teal:#1b9db3;
  --teal-dark:#147f91;
  --yellow:#f6d437;
  --ink:#2f3336;
  --muted:#7a7f84;
  --banner:#ececec;
  --line:#e2e2e2;
  --white:#ffffff;
  --footer-dark:#2a2a2a;
}
*{box-sizing:border-box;margin:0;padding:0}
html,body{width:1200px;height:2260px;overflow:hidden;background:var(--white)}
body{font-family:"Open Sans",Arial,sans-serif;color:var(--ink);position:relative}
.site-header{position:absolute;top:0;left:0;width:1200px;height:168px}
.brand{position:absolute;left:80px;top:22px;display:flex;align-items:center;gap:14px}
.brand-square{width:56px;height:56px;background:var(--yellow)}
.brand-name{font-family:"Montserrat",sans-serif;font-weight:700;font-size:22px;color:var(--teal);line-height:1.1;width:140px}
.topbar{position:absolute;right:80px;top:16px;display:flex;align-items:center;gap:26px;font-size:15px;color:var(--muted)}
.topbar .item{display:flex;align-items:center;gap:8px}
.social{display:flex;gap:10px}
.social span{width:24px;height:24px;border-radius:50%;background:var(--teal);display:block}
.main-nav{position:absolute;right:80px;top:100px;display:flex;gap:34px;font-family:"Montserrat",sans-serif;font-size:16px;font-weight:600;color:var(--ink)}
.main-nav .active{color:var(--teal)}
.page-banner{position:absolute;top:168px;left:0;width:1200px;height:132px;background:var(--banner);display:flex;align-items:center;justify-content:center}
.page-title{font-family:"Montserrat",sans-serif;font-weight:700;font-size:36px;color:var(--teal);letter-spacing:1px}
.intro-photo{position:absolute;left:80px;top:380px;width:505px;height:420px;background:linear-gradient(135deg,#d9b48f,#9c6b4a 55%,#5a4a3f)}
.intro-text{position:absolute;left:625px;top:400px;width:495px}
.section-heading{font-family:"Montserrat",sans-serif;font-weight:700;font-size:26px;color:var(--teal);margin-bottom:18px}
.intro-text p{font-size:15px;line-height:1.6;color:var(--muted);margin-bottom:16px}
.intro-text p.lead{font-weight:700;color:var(--ink)}
.feature{position:absolute;width:460px}
.feature .icon{width:92px;height:92px;border-radius:50%;background:var(--teal);display:flex;align-items:center;justify-content:center;margin-bottom:18px}
.feature h3{font-family:"Montserrat",sans-serif;font-weight:700;font-size:24px;color:var(--ink);margin-bottom:10px}
.feature p{font-size:15px;line-height:1.55;color:var(--muted)}
.divider{position:absolute;left:80px;top:1104px;width:1040px;height:2px;background:var(--line)}
.lab-intro{position:absolute;left:80px;top:1140px;width:1040px}
.lab-intro p{font-size:15px;color:var(--muted);width:900px;line-height:1.55}
.lab-feature{width:300px}
.brands{position:absolute;left:80px;top:1550px;width:1040px;display:flex;justify-content:space-between;font-family:"Montserrat",sans-serif;font-weight:700;font-size:22px;color:var(--ink)}
.frames{position:absolute;left:80px;top:1615px;width:1040px;display:flex;justify-content:space-between}
.frames span{width:130px;height:70px;border-radius:35px;background:linear-gradient(180deg,#c8c8c8,#6d6d6d)}
.site-footer{position:absolute;left:0;top:1720px;width:1200px;height:492px;background:var(--yellow)}
.footer-col{position:absolute;top:40px;width:320px}
.footer-col h4{font-family:"Montserrat",sans-serif;font-weight:700;font-size:22px;color:var(--ink);margin-bottom:22px}
.footer-col .row{display:flex;gap:12px;align-items:flex-start;font-size:15px;line-height:1.4;margin-bottom:14px;color:var(--ink)}
.dot{width:26px;height:26px;border-radius:50%;background:var(--teal);flex:none}
.map-btn{position:absolute;top:360px;background:var(--footer-dark);color:var(--white);font-size:15px;padding:12px 26px;border-radius:24px;display:flex;align-items:center;gap:40px}
.map-btn b{width:20px;height:20px;border-radius:50%;background:var(--yellow);display:block}
.footer-social{position:absolute;left:800px;top:362px;display:flex;gap:12px}
.footer-social span{width:40px;height:40px;background:var(--teal);border-radius:50%;display:block}
.copyright{position:absolute;left:0;top:2212px;width:1200px;height:48px;background:var(--white);font-size:14px;color:var(--muted);display:flex;align-items:center;justify-content:center}
.copyright strong{color:var(--teal);margin:0 4px}
</style>
</head>
<body>
<header class="site-header">
  <div class="brand"><div class="brand-square"></div><div class="brand-name">LUMIVO OPTOMETRY</div></div>
  <div class="topbar">
    <div class="item"><svg width="16" height="16" viewBox="0 0 24 24"><path d="M6.6 10.8a15 15 0 006.6 6.6l2.2-2.2a1 1 0 011-.25 11 11 0 003.6.6 1 1 0 011 1V20a1 1 0 01-1 1A17 17 0 013 4a1 1 0 011-1h3.5a1 1 0 011 1 11 11 0 00.6 3.6 1 1 0 01-.25 1z" fill="#1b9db3"/></svg>555-014-2090</div>
    <div class="item"><svg width="18" height="14" viewBox="0 0 24 18"><rect x="1" y="1" width="22" height="16" rx="2" fill="none" stroke="#1b9db3" stroke-width="2"/><path d="M1 2l11 8 11-8" fill="none" stroke="#1b9db3" stroke-width="2"/></svg>info@lumivoeyes.com</div>
    <div class="social"><span></span><span></span><span></span><span></span></div>
  </div>
  <nav class="main-nav">
    <span>HOME</span><span>OUR TEAM</span><span class="active">EYE CARE</span><span>MYOPIA CONTROL CLINIC</span><span>EYEWEAR</span><span>BLOG</span><span>CONTACT US</span>
  </nav>
</header>

<section class="page-banner"><h1 class="page-title">EYE GLASS LENSES</h1></section>

<div class="intro-photo" role="img" aria-label="Smiling couple wearing eyeglasses"></div>
<section class="intro-text">
  <h2 class="section-heading">GLASSES MADE SIMPLE</h2>
  <p class="lead">Making a decision about your eye wear goes beyond good vision and makes a statement about who you are. Your decision affects how you see and also how you want to be seen by others.</p>
  <p>Our experienced opticians will help you find the look to fit your specific needs and explain how different lenses and frames will impact your vision. They will help you narrow down your choices so you can find the look, fit and functionality you want from your eyewear. We offer a large selection of eyeglasses, contact lenses and designer frames and sunglasses. New clients and all our current patients are welcome to visit us with their current prescription - no appointment necessary.</p>
</section>

<div class="feature" style="left:80px;top:842px">
  <div class="icon"><svg width="54" height="30" viewBox="0 0 54 30"><circle cx="13" cy="17" r="10" fill="none" stroke="#fff" stroke-width="3"/><circle cx="41" cy="17" r="10" fill="none" stroke="#fff" stroke-width="3"/><path d="M23 15q4-4 8 0M3 15L1 5M51 15l2-10" fill="none" stroke="#fff" stroke-width="3"/></svg></div>
  <h3>ANY FRAME</h3>
  <p>We can put your prescription into virtually any frame, including your own previous frames. We can also use prescriptions from eyeglasses.</p>
</div>
<div class="feature" style="left:625px;top:842px">
  <div class="icon"><svg width="40" height="46" viewBox="0 0 40 46"><rect x="4" y="3" width="32" height="40" rx="3" fill="none" stroke="#fff" stroke-width="3"/><path d="M11 14h18M11 22h18M11 30h12" stroke="#fff" stroke-width="3"/></svg></div>
  <h3>OUTSIDE PRESCRIPTIONS WELCOME</h3>
  <p>We are happy to fill any outside prescriptions from other doctors.</p>
</div>

<div class="divider"></div>

<section class="lab-intro">
  <h2 class="section-heading">ON- SITE LAB</h2>
  <p>We have a full-service optical laboratory equipped with the most advanced finishing technology allowing us to manufacture your eye wear prescription in-house on site.</p>
</section>

<div class="feature lab-feature" style="left:80px;top:1254px">
  <div class="icon"><svg width="44" height="44" viewBox="0 0 44 44"><path d="M8 36L26 18a9 9 0 1110 -10l-6 6 4 4 6-6a9 9 0 01-10 10L12 40z" fill="none" stroke="#fff" stroke-width="3" stroke-linejoin="round"/></svg></div>
  <h3>ADJUSTMENTS &amp; REPAIRS</h3>
  <p>Our highly trained opticians can adjust and properly fit your frames. We offer free adjustments for anyone purchasing frames from our office.</p>
</div>
<div class="feature lab-feature" style="left:450px;top:1254px">
  <div class="icon"><svg width="44" height="44" viewBox="0 0 44 44"><circle cx="22" cy="22" r="18" fill="none" stroke="#fff" stroke-width="3"/><path d="M22 11v11l8 6" fill="none" stroke="#fff" stroke-width="3"/></svg></div>
  <h3>1- HOUR SERVICE</h3>
  <p>Our on-site optical lab is fully equipped to provide you with glasses ready within a one-hour for most prescriptions.</p>
</div>
<div class="feature lab-feature" style="left:820px;top:1254px">
  <div class="icon"><svg width="50" height="30" viewBox="0 0 50 30"><path d="M2 15Q25-9 48 15 25 39 2 15z" fill="none" stroke="#fff" stroke-width="3"/><circle cx="25" cy="15" r="7" fill="#fff"/></svg></div>
  <h3>LENS FEATURE</h3>
  <p>With reflection free, light protect, scratch resistant lens protection technology.</p>
</div>

<div class="brands"><span>VANTRO</span><span>ELM ORRIN</span><span>KESSLY &amp; CO.</span><span>MARZELLA</span><span>ORVAINE</span><span>KESTREL</span></div>
<div class="frames" role="img" aria-label="Row of designer eyeglass frames">
  <span></span><span></span><span></span><span></span><span></span><span></span>
</div>

<footer class="site-footer">
  <div class="footer-col" style="left:80px">
    <h4>Lumivo Optometry</h4>
    <div class="row"><span class="dot"></span>555-014-2090</div>
    <div class="row"><span class="dot"></span>555-014-2070</div>
    <div class="row"><span class="dot"></span>info@lumivoeyes.com</div>
    <div class="row"><span class="dot"></span>4120 Larkspur Ave, Alder Bluff,<br>CA 90011</div>
  </div>
  <div class="footer-col" style="left:440px">
    <h4>Alder Bluff</h4>
    <div class="row"><span class="dot"></span>555-019-9022</div>
    <div class="row"><span class="dot"></span>bluff@lumivoeyes.com</div>
    <div class="row"><span class="dot"></span>2850 Quarry Lane,<br>Alder Bluff, CA 90012</div>
  </div>
  <div class="footer-col" style="left:800px">
    <h4>Opening Hours</h4>
    <div class="row">Monday - Thursday: 9 am - 6 pm</div>
    <div class="row">Friday: 8.30 am - 5 pm</div>
    <div class="row">Saturday: 8.30 am - 5 pm</div>
    <div class="row">Closed on Sundays</div>
    <div class="row">Please keep in mind we are closed<br>on lunch 1-2 pm</div>
  </div>
  <div class="map-btn" style="left:80px">Get directions on the map <b></b></div>
  <div class="map-btn" style="left:440px">Get directions on the map <b></b></div>
  <div class="footer-social"><span></span><span></span><span></span><span></span></div>
</footer>
<div class="copyright">Copyright © <strong>LUMIVO OPTOMETRY</strong> 2016, all rights reserved</div>
</body>
</html>
```